Agriculture Business Card

I want to use my existing logo and use my tagline of "Don't Guess...Soil Test" on the card. Looking for a double sided card that will really get peoples attention.
Contact Info:
Marlow Field Crop Edge
Calvin Brusk
2917 K Lane
Larkin, NE 68593
402-555-0193
calvin.r.brusk@fieldmailbox.net

```html
<!DOCTYPE html>
<html lang="en">
<head>
<meta charset="utf-8">
<title>Marlow Field Crop Edge — Business Card</title>
<link href="https://fonts.googleapis.com/css2?family=Arimo:wght@400;700&family=Fira+Sans+Extra+Condensed:wght@600&display=swap" rel="stylesheet">
<style>
  :root{
    --page:#e9e9e9;
    --card:#2e2e2e;
    --card-faint:#383838;
    --brand:#a5694b;
    --green:#3cb043;
    --ink:#f2f2f2;
    --muted:#cfcfcf;
    --gold:#f0b21a;
    --rule:#bdbdbd;
  }
  *{margin:0;padding:0;box-sizing:border-box}
  html,body{width:1200px;height:802px;overflow:hidden;background:var(--page)}
  body{display:flex;align-items:center;justify-content:center;gap:40px;font-family:"Arimo",Arial,sans-serif}
  .card{position:relative;width:560px;height:320px;background:var(--card);overflow:hidden;box-shadow:0 6px 18px rgba(0,0,0,.18)}
  .mark-dot{width:22px;height:22px;border-radius:50%;background:var(--gold)}
  .faint-mark{position:absolute;border-radius:50%;background:var(--card-faint)}

  /* front */
  .front .faint-mark{left:60px;top:40px;width:230px;height:230px}
  .front .brand{position:absolute;right:34px;top:46px;display:flex;align-items:center;gap:12px}
  .front .brand-name{font-family:"Fira Sans Extra Condensed",sans-serif;font-weight:600;font-size:26px;line-height:1;color:var(--brand);text-align:right}
  .front .rule{position:absolute;left:30px;right:30px;top:206px;height:1px;background:var(--rule)}
  .front .person{position:absolute;left:34px;top:172px;font-size:25px;font-weight:400;color:var(--green);letter-spacing:.5px}
  .front .contact{position:absolute;left:34px;top:222px;list-style:none;font-size:16px;color:var(--ink);line-height:1.55}
  .front .contact li{display:flex;align-items:center;gap:8px}
  .front .contact svg{width:13px;height:13px;fill:var(--green)}
  .front .address{position:absolute;right:34px;top:222px;font-size:16px;color:var(--ink);line-height:1.55;text-align:left;font-style:normal}

  /* back */
  .back .faint-mark{left:40px;top:40px;width:250px;height:250px;background:linear-gradient(160deg,#5a5a5a,#2a2a2a)}
  .back .brand-name{position:absolute;right:36px;top:150px;font-family:"Fira Sans Extra Condensed",sans-serif;font-weight:600;font-size:34px;line-height:1;color:var(--ink);text-align:right}
  .back .tagline{position:absolute;right:36px;top:232px;font-size:17px;font-weight:700;color:var(--gold)}
</style>
</head>
<body>
  <section class="card front" aria-label="Card front">
    <div class="faint-mark" aria-hidden="true"></div>
    <div class="brand">
      <span class="mark-dot" aria-hidden="true"></span>
      <span class="brand-name">Marlow Field<br>Crop Edge</span>
    </div>
    <h1 class="person">CALVIN BRUSK</h1>
    <div class="rule"></div>
    <ul class="contact">
      <li><svg viewBox="0 0 24 24" aria-hidden="true"><path d="M6.6 10.8a15.1 15.1 0 0 0 6.6 6.6l2.2-2.2c.3-.3.7-.4 1-.2 1.1.4 2.3.6 3.6.6.6 0 1 .4 1 1V20c0 .6-.4 1-1 1A17 17 0 0 1 3 4c0-.6.4-1 1-1h3.5c.6 0 1 .4 1 1 0 1.3.2 2.5.6 3.6.1.3 0 .7-.2 1z"/></svg>402-555-0193</li>
      <li><svg viewBox="0 0 24 24" aria-hidden="true"><path d="M2 5h20v14H2zm2 2v.5l8 5 8-5V7l-8 5z"/></svg>calvin.r.brusk@fieldmailbox.net</li>
    </ul>
    <address class="address">2917 K Lane<br>Larkin, NE 68593</address>
  </section>

  <section class="card back" aria-label="Card back">
    <div class="faint-mark" role="img" aria-label="Embossed brand mark area"></div>
    <h2 class="brand-name">Marlow Field Crop<br>Edge</h2>
    <p class="tagline">Don't Guess...Soil Test</p>
  </section>
</body>
</html>
```